BOLD & MINIMALIST DESIGN NEEDED

We want a very bold but minimalistic business card design that is impactful and utilizes both sides of the business card. Our current logo is included for your use.

We want bold fonts and good use of negative space. We don't want the logo to overpower the design.

Target Market(s)

Professionals who are building new commercial buildings.

Industry/Entity Type

Construction

Contact Information for Business Card

Name, Title, email, office phone, cell phone, website

Font styles to use
Serif
Sans Serif

Requirements
Must have
• Bold design!

```html
<!DOCTYPE html>
<html lang="en">
<head>
<meta charset="utf-8">
<title>Ridgeline Design + Build – Business Card</title>
<link href="https://fonts.googleapis.com/css2?family=Montserrat:wght@500;600;800&family=Poppins:wght@400;500&display=swap" rel="stylesheet">
<style>
  :root {
    --bg: #c9c9c9;
    --green-light: #b9e285;
    --green: #8cc63f;
    --green-deep: #7cb928;
    --ink: #111111;
    --paper: #ffffff;
    --mist: #ececec;
    --mist-soft: #f6f6f6;
  }
  * { box-sizing: border-box; margin: 0; padding: 0; }
  html, body { width: 1200px; height: 900px; overflow: hidden; }
  body {
    background: var(--bg);
    font-family: "Montserrat", Arial, sans-serif;
    color: var(--ink);
    position: relative;
  }
  .card {
    position: absolute;
    left: 250px;
    width: 700px;
    height: 400px;
    border-radius: 26px;
    overflow: hidden;
    box-shadow: 0 6px 14px rgba(0,0,0,0.25);
  }
  /* Front */
  .card--front {
    top: 35px;
    background: linear-gradient(170deg, var(--green-light) 0%, var(--green) 60%, var(--green-deep) 100%);
  }
  .front-decor {
    position: absolute;
    right: 0; top: 0;
    width: 300px; height: 100%;
    background: linear-gradient(200deg, rgba(255,255,255,0.22), rgba(255,255,255,0) 70%);
  }
  .front-brand {
    position: absolute;
    inset: 0;
    display: flex;
    align-items: center;
    justify-content: center;
    gap: 14px;
  }
  .brand-mark {
    width: 22px; height: 22px;
    background: var(--ink);
  }
  .brand-name {
    font-weight: 800;
    font-size: 34px;
    letter-spacing: 1px;
    text-transform: uppercase;
    color: var(--ink);
  }
  /* Back */
  .card--back {
    top: 465px;
    background: var(--paper);
  }
  .back-decor {
    position: absolute;
    right: 0; top: 0;
    width: 360px; height: 100%;
    background: linear-gradient(160deg, var(--mist) 0%, var(--mist-soft) 55%, var(--paper) 100%);
  }
  .back-brand {
    position: absolute;
    left: 52px; top: 72px;
    display: flex;
    align-items: center;
    gap: 10px;
  }
  .back-brand .brand-name { font-size: 24px; }
  .back-brand .brand-mark { width: 16px; height: 16px; }
  .person {
    position: absolute;
    left: 52px; top: 190px;
  }
  .person-name {
    font-weight: 800;
    font-size: 26px;
    color: var(--green);
    text-transform: uppercase;
    line-height: 1.05;
  }
  .person-title {
    font-weight: 600;
    font-size: 14px;
    text-transform: uppercase;
    letter-spacing: 0.5px;
    margin-top: 2px;
  }
  .phones {
    position: absolute;
    left: 52px; top: 290px;
    list-style: none;
    font-family: "Poppins", Arial, sans-serif;
    font-size: 21px;
  }
  .phones li, .web li {
    display: flex;
    align-items: center;
    gap: 10px;
    line-height: 1.4;
  }
  .icon { width: 18px; height: 18px; flex: none; }
  .web {
    position: absolute;
    right: 36px; top: 150px;
    list-style: none;
    font-family: "Poppins", Arial, sans-serif;
    font-size: 17px;
    text-align: right;
  }
  .web li { justify-content: flex-end; }
</style>
</head>
<body>

<section class="card card--front" aria-label="Card front">
  <div class="front-decor"></div>
  <div class="front-brand">
    <span class="brand-mark"></span>
    <span class="brand-name">Ridgeline Design + Build</span>
  </div>
</section>

<section class="card card--back" aria-label="Card back">
  <div class="back-decor"></div>
  <div class="back-brand">
    <span class="brand-mark"></span>
    <span class="brand-name">Ridgeline Design + Build</span>
  </div>

  <div class="person">
    <p class="person-name">Marcus Hale</p>
    <p class="person-title">Managing Director</p>
  </div>

  <ul class="phones">
    <li>
      <svg class="icon" viewBox="0 0 24 24" aria-hidden="true"><path fill="#8cc63f" d="M6.6 10.8a15 15 0 0 0 6.6 6.6l2.2-2.2a1 1 0 0 1 1-.25 11.4 11.4 0 0 0 3.6.57 1 1 0 0 1 1 1V20a1 1 0 0 1-1 1A17 17 0 0 1 3 4a1 1 0 0 1 1-1h3.5a1 1 0 0 1 1 1c0 1.25.2 2.45.57 3.6a1 1 0 0 1-.25 1z"/></svg>
      044-555 210 340
    </li>
    <li>
      <svg class="icon" viewBox="0 0 24 24" aria-hidden="true"><rect x="6" y="2" width="12" height="20" rx="2" fill="none" stroke="#8cc63f" stroke-width="2"/><circle cx="12" cy="18" r="1.2" fill="#8cc63f"/></svg>
      044-555 210 341
    </li>
  </ul>

  <ul class="web">
    <li>
      info@ridgelinebuild.com
      <svg class="icon" viewBox="0 0 24 24" aria-hidden="true"><rect x="2" y="5" width="20" height="14" rx="1.5" fill="#8cc63f"/><path d="M3 6l9 7 9-7" fill="none" stroke="#fff" stroke-width="1.6"/></svg>
    </li>
    <li>
      www.ridgelinebuild.com
      <svg class="icon" viewBox="0 0 24 24" aria-hidden="true"><circle cx="12" cy="12" r="9" fill="none" stroke="#8cc63f" stroke-width="2"/><path d="M3 12h18M12 3c3 3 3 15 0 18M12 3c-3 3-3 15 0 18" fill="none" stroke="#8cc63f" stroke-width="1.6"/></svg>
    </li>
  </ul>
</section>

</body>
</html>
```